Business Card Design Competition

We need a business card design for our Internet Marketing company. We require both front and back designs and the final card must be 89x53mm in size, plus crop marks to 91x55mm. Colours as per logo, plus perhaps black and/or grey (#828282).
Final text must be editable (if you can supply an editable Fireworks PNG, even better)...
FRONT TEXT:
Full Name
Position
Address Line
Suburb, State, Postcode
Phone: 0000 000 000
Mobile: 0000 000 000
Email: xxx@brightlanemedia.com.au
Web: www.brightlanemedia.com.au
Rear of card should be a fresh design plus our slogan text: "Putting You Forward" in large font, then in small text "Kestrel Holdings Pty Ltd (ABN: 42 561 903 774)".
Target Market(s)
Small/Medium Businesses
Industry/Entity Type
Business

```html
<!DOCTYPE html>
<html lang="en">
<head>
<meta charset="utf-8">
<title>Brightlane Media – Business Card</title>
<link rel="stylesheet" href="https://fonts.googleapis.com/css2?family=Ubuntu:wght@400;500&family=Oswald:wght@500&family=Arimo&display=swap">
<style>
  :root {
    --backdrop: #3a3a3a;
    --card-white: #ffffff;
    --brand-green: #8cc63f;
    --brand-orange: #f7941d;
    --back-orange: #faa72c;
    --ink: #1f1f1f;
  }
  * { box-sizing: border-box; margin: 0; padding: 0; }
  html, body { width: 1200px; height: 900px; overflow: hidden; }
  body { background: var(--backdrop); position: relative; font-family: "Ubuntu", sans-serif; }

  .card { position: absolute; border-radius: 20px; overflow: hidden; }

  /* Front */
  .card-front { left: 232px; top: 75px; width: 675px; height: 372px; background: var(--card-white); }
  .brand { position: absolute; display: flex; align-items: center; gap: 10px; }
  .brand-dot { width: 44px; height: 44px; border-radius: 50%; background: var(--brand-orange); flex: none; }
  .brand-name { font-family: "Ubuntu", sans-serif; font-weight: 500; color: var(--brand-green); white-space: nowrap; }
  .card-front .brand { left: 14px; top: 28px; }
  .card-front .brand-name { font-size: 27px; }

  .holder { position: absolute; right: 27px; top: 22px; text-align: center; }
  .holder-name { font-weight: 500; font-size: 24px; color: var(--brand-green); }
  .holder-role { font-size: 15px; color: var(--brand-orange); margin-top: 4px; }

  .contacts { position: absolute; left: 16px; top: 191px; list-style: none; }
  .contacts li { display: flex; align-items: center; height: 25.5px; font-size: 15.5px; color: var(--ink); }
  .contacts svg { width: 20px; height: 18px; margin-right: 10px; fill: var(--brand-green); }

  .web-band { position: absolute; left: 0; top: 319px; width: 578px; height: 26px; background: var(--brand-green);
    color: #fff; font-size: 17px; line-height: 26px; text-align: center; letter-spacing: 0.5px; }
  .corner-dot { position: absolute; left: 585px; top: 287px; width: 98px; height: 98px; border-radius: 50%;
    background: var(--brand-green); }

  /* Back */
  .card-back { left: 237px; top: 477px; width: 669px; height: 366px; background: var(--back-orange); }
  .back-panel { position: absolute; left: 75px; top: 67px; width: 518px; height: 209px; background: var(--card-white);
    border: 3px solid var(--brand-orange); border-radius: 22px; box-shadow: 0 10px 28px rgba(120,60,0,0.45);
    display: flex; flex-direction: column; align-items: center; justify-content: center; gap: 22px; }
  .back-panel .brand { position: static; }
  .back-panel .brand-dot { width: 62px; height: 62px; }
  .back-panel .brand-name { font-size: 40px; }
  .slogan { font-family: "Oswald", sans-serif; font-weight: 500; font-size: 34px; color: var(--brand-green); letter-spacing: 0.5px; }
  .company-line { position: absolute; left: 0; right: 0; top: 322px; text-align: center; font-family: "Arimo", sans-serif;
    font-size: 21px; color: #fff; }
</style>
</head>
<body>

<section class="card card-front" aria-label="Card front">
  <div class="brand"><span class="brand-dot"></span><span class="brand-name">Brightlane Media</span></div>
  <div class="holder">
    <p class="holder-name">Your Name Here</p>
    <p class="holder-role">Manager</p>
  </div>
  <ul class="contacts">
    <li><svg viewBox="0 0 20 18"><path d="M10 1 1 9h3v8h5v-5h2v5h5V9h3z"/></svg>Address Line, Suburb, State, Postcode</li>
    <li><svg viewBox="0 0 20 18"><path d="M2 6c0-3 4-4 8-4s8 1 8 4l-1 2h-3l-1-2H7L6 8H3zM5 9h10l2 7H3z"/></svg>0000 000 000</li>
    <li><svg viewBox="0 0 20 18"><path d="M7 0h6a1 1 0 0 1 1 1v16a1 1 0 0 1-1 1H7a1 1 0 0 1-1-1V1a1 1 0 0 1 1-1zm1 3v6h4V3z"/></svg>0000 000 000</li>
    <li><svg viewBox="0 0 20 18"><path d="M1 3h18v12H1zm1.5 1.5L10 10l7.5-5.5" /></svg>name@brightlanemedia.com.au</li>
  </ul>
  <div class="web-band">www.brightlanemedia.com.au</div>
  <span class="corner-dot"></span>
</section>

<section class="card card-back" aria-label="Card back">
  <div class="back-panel">
    <div class="brand"><span class="brand-dot"></span><span class="brand-name">Brightlane Media</span></div>
    <p class="slogan">Putting You Forward</p>
  </div>
  <p class="company-line">Kestrel Holdings Pty Ltd (ABN: 42 561 903 774)</p>
</section>

</body>
</html>
```